Business Card Makeover. Recreate a sleek modern design for our business card.

DO NOT COPY OUR CURRENT DESIGN. MUST BE ONE SIDED BUSINESS CARD.
Create a new business card design, using our new logo. Attached is a sample of our current design and new logo. Please note the address and email will change. The new address is 412 Corvell West Palm Beach 33401 and our website will be www.delmarhollis.example.

We are an architectural and interior design firm. We prefer a clean modern look. Something that is refined and emulates excellence.

Industry/Entity Type

Architecture

Contact Information for Business Card

clean modern look, please do not copy our attached design.

Font styles to use
Other font styles liked:
• see attached business card font

Colors

Designer to choose colors to be used in the design.

Requirements
Must have
• Must have a modern appeal and resemble our current branding.
Nice to have
• modern font, our logo, legible name and titles progressive design
Should not have
• Do not add colors not reflected in our branding. Should not look like our current card.

```html
<!DOCTYPE html>
<html lang="en">
<head>
<meta charset="utf-8">
<title>Delmar Hollis + Partners — Business Card</title>
<link href="https://fonts.googleapis.com/css2?family=Poppins:wght@300;400&display=swap" rel="stylesheet">
<style>
  :root {
    --page-bg: #dcdcdc;
    --card-bg: #f5f5f5;
    --brand-blue: #0a73bd;
    --text-dark: #4a4a4a;
    --text-grey: #8a8a8a;
  }
  html, body {
    margin: 0;
    width: 1200px;
    height: 923px;
    overflow: hidden;
    background: var(--page-bg);
    font-family: "Poppins", Arial, sans-serif;
  }
  .card {
    position: absolute;
    left: 60px;
    top: 153px;
    width: 1080px;
    height: 617px;
    background: var(--card-bg);
    overflow: hidden;
  }
  .brand {
    position: absolute;
    left: 59px;
    top: 66px;
    display: flex;
    align-items: center;
    gap: 20px;
  }
  .brand-dot {
    width: 92px;
    height: 92px;
    border-radius: 50%;
    background: var(--brand-blue);
  }
  .brand-name {
    margin: 0;
    font-size: 37px;
    font-weight: 400;
    color: var(--text-dark);
    letter-spacing: 0.5px;
    line-height: 1.1;
  }
  .brand-tagline {
    margin: 8px 0 0;
    font-size: 19.5px;
    font-weight: 400;
    color: var(--text-grey);
    letter-spacing: 0.4px;
  }
  .address {
    position: absolute;
    left: 84px;
    top: 247px;
    margin: 0;
    font-size: 25px;
    line-height: 30px;
    font-weight: 400;
    color: var(--text-dark);
  }
  .contact-list {
    position: absolute;
    left: 84px;
    top: 327px;
    margin: 0;
    padding: 0;
    list-style: none;
  }
  .contact-item {
    display: flex;
    align-items: center;
    height: 40.5px;
    font-size: 26px;
    color: var(--text-dark);
  }
  .contact-icon {
    width: 20px;
    height: 20px;
    margin-right: 16px;
    fill: var(--brand-blue);
    flex: none;
  }
  .licence {
    position: absolute;
    left: 84px;
    top: 496px;
    margin: 0;
    font-size: 25px;
    color: var(--text-dark);
  }
  .person {
    position: absolute;
    right: 62px;
    top: 330px;
    text-align: right;
  }
  .person-name {
    margin: 0;
    font-size: 31px;
    font-weight: 400;
    color: var(--brand-blue);
    line-height: 1.15;
  }
  .person-credentials {
    font-size: 21px;
  }
  .person-title {
    margin: 2px 0 0;
    font-size: 24px;
    font-weight: 400;
    color: var(--text-grey);
  }
  .accent-tab {
    position: absolute;
    right: 0;
    top: 343px;
    width: 24px;
    height: 54px;
    background: var(--brand-blue);
  }
  .base-band {
    position: absolute;
    left: 0;
    bottom: 0;
    width: 100%;
    height: 19px;
    background: var(--brand-blue);
  }
</style>
</head>
<body>
  <main class="card">
    <header class="brand">
      <div class="brand-dot"></div>
      <div class="brand-text">
        <p class="brand-name">DELMAR HOLLIS + PARTNERS</p>
        <p class="brand-tagline">ARCHITECTURE + INTERIOR DESIGN</p>
      </div>
    </header>

    <p class="address">412 Corvell West<br>Palm Beach 33401</p>

    <ul class="contact-list">
      <li class="contact-item">
        <svg class="contact-icon" viewBox="0 0 24 24"><path d="M6.6 10.8a15.2 15.2 0 0 0 6.6 6.6l2.2-2.2a1 1 0 0 1 1-.25 11.4 11.4 0 0 0 3.6.6 1 1 0 0 1 1 1V20a1 1 0 0 1-1 1A17 17 0 0 1 3 4a1 1 0 0 1 1-1h3.5a1 1 0 0 1 1 1c0 1.25.2 2.45.6 3.6a1 1 0 0 1-.25 1z"/></svg>
        561.555.0144
      </li>
      <li class="contact-item">
        <svg class="contact-icon" viewBox="0 0 24 24"><path d="M7 2h10v6H7z M3 10h18v9H3z M6 15h12v7H6z" fill-rule="evenodd"/></svg>
        561.555.0187
      </li>
      <li class="contact-item">
        <svg class="contact-icon" viewBox="0 0 24 24"><path d="M2 5h20v14H2z M3.5 6.5 12 13l8.5-6.5" fill-rule="evenodd"/><path d="M3 6.5 12 13.2 21 6.5" fill="none" stroke="#f5f5f5" stroke-width="1.5"/></svg>
        lena@delmarhollis.example
      </li>
      <li class="contact-item">
        <svg class="contact-icon" viewBox="0 0 24 24"><circle cx="12" cy="12" r="10"/><path d="M7 7c2 1 3 3 2 5s1 3 2 4M15 4c-1 2 0 3 2 3s3 2 2 4" fill="none" stroke="#f5f5f5" stroke-width="1.6"/></svg>
        www.delmarhollis.example
      </li>
    </ul>

    <p class="licence">LIC.# AA26004817</p>

    <section class="person">
      <h1 class="person-name">LENA MARSH, <span class="person-credentials">AIA, LEED AP</span></h1>
      <p class="person-title">Partner/ Project Architect</p>
    </section>
    <div class="accent-tab"></div>

    <div class="base-band"></div>
  </main>
</body>
</html>
```